Realty Group Needs Classy, Contemporary Letterhead Design

We need a letterhead design for a new realty company located in NY, USA. We buy investment properties to rehabilitate and or keep in our rental portfolio.

```html
<!DOCTYPE html>
<html lang="en">
<head>
<meta charset="utf-8">
<title>Halden Realty Group — Letterhead</title>
<link rel="stylesheet" href="https://fonts.googleapis.com/css2?family=Montserrat:wght@500;600;800&family=Source+Sans+3:wght@400&display=swap">
<style>
  :root {
    --brand-purple: #4f2d87;
    --brand-grey: #7f7f7f;
    --ink: #333333;
    --ink-dark: #111111;
    --paper: #ffffff;
    --backdrop: #e2e2e2;
  }
  * { box-sizing: border-box; margin: 0; padding: 0; }
  html, body { width: 1200px; height: 1200px; overflow: hidden; background: var(--backdrop); }
  .letterhead {
    position: absolute; left: 204px; top: 40px;
    width: 792px; height: 1120px;
    background: var(--paper);
    font-family: "Source Sans 3", "Myriad Pro", sans-serif;
    color: var(--ink);
  }
  .band-top { position: absolute; left: 0; top: 0; width: 100%; height: 13px; background: var(--brand-purple); }
  .band-bottom { position: absolute; left: 0; bottom: 0; width: 100%; height: 23px; background: var(--brand-grey); }

  .brand { position: absolute; top: 92px; left: 0; width: 100%; text-align: center; }
  .brand-name {
    font-family: "Montserrat", sans-serif; font-weight: 800;
    font-size: 58px; line-height: 1; letter-spacing: -1px;
    color: var(--brand-purple);
  }
  .brand-tagline {
    margin: 6px auto 0; width: 320px;
    display: flex; align-items: center; gap: 10px;
    font-family: "Montserrat", sans-serif; font-weight: 600;
    font-size: 17px; letter-spacing: 1px; color: var(--brand-grey);
  }
  .brand-tagline::before, .brand-tagline::after {
    content: ""; flex: 1; height: 2px; background: var(--brand-grey);
  }

  .recipient { position: absolute; left: 74px; top: 232px; font-size: 15.5px; line-height: 21.4px; }
  .salutation { position: absolute; left: 74px; top: 381px; font-size: 15.5px; }
  .body-copy { position: absolute; left: 74px; top: 424px; width: 650px; font-size: 15.5px; line-height: 21.4px; }

  .signature {
    position: absolute; left: 248px; top: 935px; width: 296px; height: 70px;
    background: linear-gradient(90deg, #f1f1f1, #e6e6e6, #f1f1f1);
    border-radius: 4px;
  }
  .signature-rule { position: absolute; left: 114px; top: 1020px; width: 564px; height: 1.5px; background: var(--ink-dark); }

  .footer-address {
    position: absolute; left: 0; top: 1032px; width: 100%; text-align: center;
    font-family: "Montserrat", sans-serif; font-weight: 600; font-size: 14px; color: var(--ink-dark);
  }
  .footer-contacts {
    position: absolute; left: 0; top: 1059px; width: 100%;
    display: flex; justify-content: center; gap: 9px;
    font-family: "Montserrat", sans-serif; font-weight: 500; font-size: 11px; color: var(--ink-dark);
  }
  .contact-item { display: flex; align-items: center; gap: 3px; }
  .contact-item svg { width: 10px; height: 10px; fill: var(--brand-purple); }
</style>
</head>
<body>
  <main class="letterhead">
    <div class="band-top"></div>

    <header class="brand">
      <div class="brand-name">HALDEN</div>
      <div class="brand-tagline">Realty Group, LLC</div>
    </header>

    <address class="recipient" style="font-style:normal">
      Mr. John Doe<br>President<br>Strategy Accountants<br>111 Street Name,<br>City State, 12345
    </address>

    <p class="salutation">Dear</p>

    <div class="body-copy">
      <p>Lorem ipsum dolor sit amet, consectetur adipiscing elit. Aenean ut ipsum eget massa hendrerit vestibulum vel in velit. Donec pretium neque velit.</p>
      <p>Aliquam porta lectus nec mauris ornare venenatis. Vivamus non est turpis, et cursus sem. Mauris vehicula erat in diam auctor at bibendum nisl lacinia.</p>
      <p>Morbi imperdiet neque vehicula nunc convallis gravida. Vestibulum iaculis pretium placerat. Integer consequat, est sit amet facilisis eleifend, nibh nibh varius orci, eget dapibus arcu dui non purus. Pellentesque in magna mauris. Duis enim sapien, dictum vitae condimentum a, pulvinar vel lacus. Mauris et molestie nibh. Vestibulum vitae nulla at metus elementum porta sit amet interdum elit. Nulla sollicitudin neque eu nulla volutpat congue.</p>
      <p>Etiam pellentesque, velit id dapibus fermentum, turpis sapien ornare dui, ac tincidunt ligula odio congue purus. Nunc sed ante dui, in porta lectus. Cras nec sem lorem. In hac habitasse platea dictumst. Maecenas id diam quis dui porta tristique. Sed id egestas felis. Donec ullamcorper mattis posuere. Phasellus fermentum eleifend tortor vel dapibus. Vestibulum ante ipsum.</p>
    </div>

    <div class="signature" role="img" aria-label="Handwritten signature of Jonathan Doe"></div>
    <div class="signature-rule"></div>

    <div class="footer-address">218 Harbor Point Ave, Suite 004 Albany NY 12207</div>

    <div class="footer-contacts">
      <span class="contact-item">
        <svg viewBox="0 0 10 10"><path d="M2 0.5 L3.6 2.6 L2.8 3.6 Q4 6 6.4 7.2 L7.4 6.4 L9.5 8 L8.4 9.5 Q1.5 8 0.5 1.6 Z"/></svg>555.210.4400
      </span>
      <span class="contact-item">
        <svg viewBox="0 0 10 10"><rect x="2.5" y="0.5" width="5" height="9" rx="1" fill="none" stroke="#4f2d87" stroke-width="1"/></svg>555.318.2090
      </span>
      <span class="contact-item">
        <svg viewBox="0 0 10 10"><rect x="2.5" y="0.5" width="5" height="3"/><rect x="0.5" y="3.5" width="9" height="4" rx="1"/><rect x="2.5" y="7" width="5" height="2.5"/></svg>555.627.7315
      </span>
      <span class="contact-item">
        <svg viewBox="0 0 10 10"><rect x="0.5" y="2" width="9" height="6.5"/><path d="M0.5 2 L5 5.5 L9.5 2" fill="none" stroke="#fff" stroke-width="0.9"/></svg>jonathan@haldenrealty.com
      </span>
      <span class="contact-item">
        <svg viewBox="0 0 10 10"><g fill="none" stroke="#4f2d87" stroke-width="0.9"><circle cx="5" cy="5" r="4.4"/><ellipse cx="5" cy="5" rx="2" ry="4.4"/><path d="M0.6 5 H9.4 M1.3 2.8 H8.7 M1.3 7.2 H8.7"/></g></svg>www.haldenrealty.com
      </span>
    </div>

    <div class="band-bottom"></div>
  </main>
</body>
</html>
```